MS word document templates for consultancy

I need the following templates for my business using my logo as branding.

- General report template
- Letter head template
- Tender proposal template

The templates should be sleek and with minimal colors, but with a small amount of green and grey where appropriate (as per attached logo and email signature). Font should be consistent with the text in the email signature.

```html
<!DOCTYPE html>
<html lang="en">
<head>
<meta charset="utf-8">
<title>Northbound Advisory – Stationery Templates</title>
<link rel="stylesheet" href="https://fonts.googleapis.com/css2?family=Roboto:wght@300;400;500;700&display=swap">
<style>
  :root {
    --bg-top: #595959;
    --bg-mid: #808080;
    --paper: #ededed;
    --paper-light: #f6f6f6;
    --green: #1f8a3a;
    --grey-bar: #8c8c8c;
    --ink: #1c1c1c;
    --text-grey: #6f6f6f;
    --title-grey: #7a7a7a;
  }
  * { margin: 0; padding: 0; box-sizing: border-box; }
  html, body { width: 1200px; height: 2526px; overflow: hidden; }
  body { font-family: "Roboto", Arial, sans-serif; position: relative; }

  .section { position: absolute; left: 0; width: 1200px; }
  .section--letter { top: 0; height: 902px; background: var(--bg-top); }
  .section--report { top: 902px; height: 803px; background: var(--bg-mid); }
  .section--tender { top: 1705px; height: 821px; background: var(--bg-mid); }

  /* Letterhead */
  .letterhead {
    position: absolute; left: 397px; top: 150px; width: 413px; height: 580px;
    background: linear-gradient(var(--paper) 0 33%, var(--paper-light) 33% 67%, #fafafa 67%);
    box-shadow: 0 10px 24px rgba(0,0,0,.35);
  }
  .bar-green { position: absolute; height: 9px; background: var(--green); }
  .bar-grey { position: absolute; height: 9px; background: var(--grey-bar); }
  .brand {
    position: absolute; font-weight: 400; color: var(--ink); white-space: nowrap;
    display: flex; align-items: center; gap: 6px;
  }
  .brand__dot { width: 8px; height: 8px; background: var(--green); }
  .letterhead .brand { left: 40px; top: 28px; font-size: 19px; }
  .subject { position: absolute; left: 42px; top: 130px; font-size: 12px; font-weight: 500; color: var(--text-grey); letter-spacing: .5px; }
  .sender-name { position: absolute; left: 42px; top: 162px; font-size: 11px; font-weight: 700; color: var(--green); }
  .sender-role { position: absolute; left: 42px; top: 178px; font-size: 8.5px; color: var(--green); }
  .body-copy { position: absolute; left: 42px; top: 207px; width: 321px; font-size: 6px; line-height: 8.8px; color: var(--text-grey); font-weight: 300; text-align: justify; }
  .body-copy p { margin-bottom: 17px; }
  .signature { position: absolute; left: 286px; top: 428px; width: 86px; height: 22px; background: linear-gradient(90deg, #e4e4e4, #d2d2d2, #e4e4e4); }
  .sign-date { position: absolute; left: 305px; top: 454px; font-size: 8.5px; color: #444; }
  .contact-phone { position: absolute; left: 0; width: 413px; top: 543px; text-align: center; font-size: 7.5px; font-weight: 500; color: var(--green); }
  .contact-row { position: absolute; left: 18px; right: 16px; top: 555px; display: flex; justify-content: space-between; font-size: 7.5px; font-weight: 500; color: var(--green); }
  .contact-row .sep { color: #bbb; }

  /* Covers */
  .cover {
    position: absolute; left: 435px; width: 330px; height: 460px;
    background: var(--paper); box-shadow: 0 10px 24px rgba(0,0,0,.3);
  }
  .section--report .cover { top: 170px; }
  .section--tender .cover { top: 180px; }
  .cover .brand { left: 30px; top: 40px; font-size: 20px; }
  .cover__year { position: absolute; left: 30px; top: 72px; font-size: 22px; color: var(--title-grey); }
  .cover__title { position: absolute; left: 0; width: 330px; top: 190px; text-align: center; font-size: 30px; line-height: 32px; color: var(--title-grey); }
  .cover__title strong { display: block; font-weight: 700; }
  .cover__title span { display: block; font-weight: 300; }
  .cover__phone { position: absolute; left: 0; width: 330px; top: 420px; text-align: center; font-size: 6px; color: var(--green); }
  .cover__contacts { position: absolute; left: 14px; right: 12px; top: 430px; display: flex; justify-content: space-between; font-size: 6px; color: var(--green); }
</style>
</head>
<body>

<section class="section section--letter">
  <article class="letterhead">
    <div class="bar-green" style="left:144px;top:0;width:126px"></div>
    <div class="brand"><span>Northbound Advisory</span><span class="brand__dot"></span></div>
    <div class="subject">SUBJECT</div>
    <div class="sender-name">DANIEL REYES</div>
    <div class="sender-role">Managing Director</div>
    <div class="body-copy">
      <p>Lorem ipsum dolor sit amet, consectetur adipiscing elit, sed do eiusmod tempor incididunt ut labore et dolore magna aliqua. Ut enim ad minim veniam, quis nostrud exercitation ullamco laboris nisi ut aliquip ex ea commodo consequat. Duis aute irure dolor in reprehenderit in voluptate velit esse cillum dolore eu fugiat nulla pariatur. Excepteur sint occaecat cupidatat non proident, sunt in culpa qui officia deserunt mollit anim id est laborum. Sed ut perspiciatis unde omnis iste natus error sit voluptatem accusantium doloremque laudantium.</p>
      <p>Nemo enim ipsam voluptatem quia voluptas sit aspernatur aut odit aut fugit, sed quia consequuntur magni dolores eos qui ratione voluptatem sequi nesciunt.</p>
      <p>Neque porro quisquam est, qui dolorem ipsum quia dolor sit amet, consectetur, adipisci velit, sed quia non numquam eius modi tempora incidunt ut labore et dolore magnam aliquam quaerat voluptatem. Ut enim ad minima veniam, quis nostrum exercitationem ullam corporis.</p>
      <p>At vero eos et accusamus et iusto odio dignissimos ducimus qui blanditiis praesentium voluptatum deleniti atque corrupti quos dolores et quas molestias.</p>
    </div>
    <div class="signature" role="img" aria-label="Handwritten signature of the sender"></div>
    <div class="sign-date">23/01/2025</div>
    <div class="contact-phone">0400 555 310</div>
    <div class="contact-row">
      <span>Dummy City, Dummy Country</span><span class="sep">|</span>
      <span>www.northboundadvisory.com</span><span class="sep">|</span>
      <span>hello@northboundadvisory.com</span>
    </div>
    <div class="bar-grey" style="left:0;bottom:0;width:144px"></div>
    <div class="bar-green" style="left:144px;bottom:0;width:126px"></div>
    <div class="bar-grey" style="left:270px;bottom:0;width:143px"></div>
  </article>
</section>

<section class="section section--report">
  <article class="cover">
    <div class="bar-green" style="left:110px;top:0;width:110px;height:8px"></div>
    <div class="brand"><span>Northbound Advisory</span><span class="brand__dot"></span></div>
    <div class="cover__year">2025</div>
    <div class="cover__title"><strong>GENERAL</strong><span>REPORT</span></div>
    <div class="cover__phone">0400 555 310</div>
    <div class="cover__contacts"><span>Dummy City, Dummy Country</span><span>www.northboundadvisory.com</span><span>hello@northboundadvisory.com</span></div>
    <div class="bar-grey" style="left:0;bottom:0;width:110px;height:8px"></div>
    <div class="bar-green" style="left:110px;bottom:0;width:110px;height:8px"></div>
    <div class="bar-grey" style="left:220px;bottom:0;width:110px;height:8px"></div>
  </article>
</section>

<section class="section section--tender">
  <article class="cover">
    <div class="bar-green" style="left:110px;top:0;width:110px;height:8px"></div>
    <div class="brand"><span>Northbound Advisory</span><span class="brand__dot"></span></div>
    <div class="cover__year">2025</div>
    <div class="cover__title"><strong>TENDER</strong><span>PROPOSAL</span></div>
    <div class="cover__phone">0400 555 310</div>
    <div class="cover__contacts"><span>Dummy City, Dummy Country</span><span>www.northboundadvisory.com</span><span>hello@northboundadvisory.com</span></div>
    <div class="bar-grey" style="left:0;bottom:0;width:110px;height:8px"></div>
    <div class="bar-green" style="left:110px;bottom:0;width:110px;height:8px"></div>
    <div class="bar-grey" style="left:220px;bottom:0;width:110px;height:8px"></div>
  </article>
</section>

</body>
</html>
```